Business card design for my company.
I would like the card's background colour to be black. You can also see our web site to get an idea of our brand. https://www.tmwhomecrafting.com.au/
- Name
- Email

```html
<!DOCTYPE html>
<html lang="en">
<head>
<meta charset="utf-8">
<title>TMW Home Crafting – Business Card</title>
<link rel="stylesheet" href="https://fonts.googleapis.com/css2?family=Open+Sans:wght@400;600;700&display=swap">
<style>
  :root {
    --canvas: #2b2b2d;
    --card: #1a1a1b;
    --green: #159a3c;
    --white: #f4f4f4;
    --rule: #d9d9d9;
    --emboss: #3b3b3d;
  }
  * { box-sizing: border-box; margin: 0; padding: 0; }
  html, body { width: 1200px; height: 1088px; overflow: hidden; }
  body {
    background: var(--canvas);
    font-family: "Open Sans", Arial, sans-serif;
    position: relative;
  }
  .card {
    position: absolute;
    width: 760px;
    height: 434px;
    background: var(--card);
    overflow: hidden;
    box-shadow: 0 18px 40px rgba(0,0,0,.45);
  }
  .card--front { left: 110px; top: 70px; }
  .card--back  { left: 330px; top: 584px; }

  /* front */
  .brand {
    position: absolute;
    right: 70px;
    top: 62px;
    display: flex;
    align-items: center;
    gap: 14px;
  }
  .brand__mark { width: 22px; height: 22px; background: var(--green); }
  .brand__name {
    color: var(--white);
    font-weight: 700;
    font-size: 30px;
    letter-spacing: 3px;
  }
  .divider {
    position: absolute;
    left: 150px;
    right: 40px;
    top: 166px;
    height: 1px;
    background: var(--rule);
  }
  .person { position: absolute; left: 120px; top: 188px; }
  .person__name {
    color: var(--green);
    font-weight: 700;
    font-size: 22px;
    letter-spacing: .5px;
  }
  .person__title { color: var(--white); font-size: 17px; }
  .person__rule {
    width: 250px;
    height: 1px;
    background: var(--rule);
    margin: 14px 0 16px;
  }
  .contact { list-style: none; color: var(--white); font-size: 17px; line-height: 26px; }
  .contact li { display: flex; align-items: center; gap: 8px; }
  .contact svg { width: 14px; height: 14px; fill: var(--green); }
  .location {
    position: absolute;
    right: 46px;
    top: 250px;
    text-align: right;
    color: var(--white);
    font-size: 16px;
    line-height: 21px;
  }
  .band { position: absolute; left: 0; bottom: 0; width: 760px; height: 120px; }
  .website {
    position: absolute;
    right: 46px;
    bottom: 22px;
    color: var(--white);
    font-size: 16px;
    line-height: 22px;
    letter-spacing: .3px;
  }

  /* back */
  .back-brand {
    position: absolute;
    inset: 0;
    display: flex;
    align-items: center;
    justify-content: center;
    gap: 18px;
  }
  .back-brand__mark { width: 34px; height: 34px; background: var(--emboss); }
  .back-brand__name {
    color: var(--emboss);
    font-weight: 700;
    font-size: 44px;
    letter-spacing: 5px;
  }
</style>
</head>
<body>
  <section class="card card--front">
    <div class="brand">
      <span class="brand__mark"></span>
      <span class="brand__name">TMW HOME CRAFTING</span>
    </div>
    <div class="divider"></div>

    <div class="person">
      <p class="person__name">DANIEL HARPER</p>
      <p class="person__title">Managing Director</p>
      <div class="person__rule"></div>
      <ul class="contact">
        <li>
          <svg viewBox="0 0 24 24" aria-hidden="true"><path d="M6.6 10.8a15.1 15.1 0 0 0 6.6 6.6l2.2-2.2c.3-.3.7-.4 1-.2 1.1.4 2.3.6 3.6.6.6 0 1 .4 1 1V20c0 .6-.4 1-1 1A17 17 0 0 1 3 4c0-.6.4-1 1-1h3.5c.6 0 1 .4 1 1 0 1.3.2 2.5.6 3.6.1.3 0 .7-.2 1z"/></svg>
          0400 123 456
        </li>
        <li>
          <svg viewBox="0 0 24 24" aria-hidden="true"><path d="M2 5h20v14H2zm2 2v.5l8 5 8-5V7l-8 5z"/></svg>
          info@tmwhomecrafting.com.au
        </li>
      </ul>
    </div>

    <p class="location">Kestrel Bay, Norvale<br>Eastmere</p>

    <svg class="band" viewBox="0 0 760 120" preserveAspectRatio="none" aria-hidden="true">
      <path d="M0 108 L392 108 Q410 108 418 90 L426 72 Q434 56 452 56 L760 56 L760 0 L760 120 L0 120 Z" fill="var(--green)"/>
      <path d="M0 98 L380 98 Q392 98 398 88 L404 76 L396 76 Q390 88 378 88 L0 88 Z" fill="var(--white)"/>
    </svg>
    <p class="website">www.tmwhomecrafting.com.au</p>
  </section>

  <section class="card card--back">
    <div class="back-brand">
      <span class="back-brand__mark"></span>
      <span class="back-brand__name">TMW HOME CRAFTING</span>
    </div>
  </section>
</body>
</html>
```